Business card design for sustainable building and development company

Need a business card design for a new sustainable building and real estate development company in the San Francisco Bay area. Name of company is "Tovrin Advisors, LLC" and we provide "Sustainable building, energy and development services" for residential and non residential projects. We'd like the following colors used but not all area required: green, gray, blue. Design should communicate innovation, professionalism and sustainability. Our current website is www.tovrin-advisors.example. Another possible design idea is to have the following listed on the back of the card:
Certified: VERN QS, Eco Marker Rater, DOLM Rater, Terravue Inspector, KSO TQ Building Analyst. Its not a must but could be text that could be used for back of card. Overall, we are open to a simple, clean design and or one with more text than usual for a card.

Industry/Entity Type

Real Estate

Contact Information for Business Card

Name on card: Mark J. Halvik
Title for Name: Principal + Founder
Phone: 555.814.0627
Email: mhalvik@tovrin-advisors.example
Website: www.tovrin-advisors.example

Also, please add the following for address:
San Francisco, California

Requirements
Nice to have
• If you can integrate the outline of a skyline on the backside of the card and if it looks good, I would like to see the design
Should not have
• a barcode;

```html
<!DOCTYPE html>
<html lang="en">
<head>
<meta charset="utf-8">
<title>Tovrin Advisors — Business Card</title>
<link href="https://fonts.googleapis.com/css2?family=Exo+2:wght@400;500;700&display=swap" rel="stylesheet">
<style>
  :root {
    --bg: #e4e4e4;
    --card: #ffffff;
    --green: #6bbd45;
    --ink: #1f1f1f;
    --ink-soft: #3a3a3a;
    --white: #ffffff;
  }
  * { margin: 0; padding: 0; box-sizing: border-box; }
  html, body {
    width: 1200px; height: 900px; overflow: hidden;
    background: var(--bg);
    font-family: "Exo 2", sans-serif;
  }
  .stage { position: relative; width: 1200px; height: 900px; }
  .card {
    position: absolute; left: 75px; top: 150px;
    width: 1050px; height: 600px;
    background: var(--card);
    overflow: hidden;
    box-shadow: 0 18px 40px rgba(0,0,0,0.18);
  }
  .card-shapes { position: absolute; inset: 0; }
  .corner-tab { fill: var(--ink); }
  .swoosh-dark { fill: var(--ink); }
  .swoosh-green { fill: var(--green); }

  .brand { position: absolute; left: 90px; top: 175px; }
  .brand-row { display: flex; align-items: center; gap: 16px; }
  .brand-dot { width: 34px; height: 34px; border-radius: 50%; background: var(--green); }
  .brand-name { font-weight: 700; font-size: 48px; color: var(--green); line-height: 1; }
  .brand-tagline {
    margin-top: 8px; margin-left: 50px;
    font-size: 12.5px; font-weight: 500; letter-spacing: 0.6px;
    text-transform: uppercase; color: var(--ink-soft);
  }

  .person { position: absolute; right: 70px; top: 62px; text-align: right; }
  .person-name { font-size: 36px; font-weight: 500; letter-spacing: 3px; color: var(--ink); line-height: 1.1; }
  .person-title { font-size: 20px; font-weight: 400; color: var(--ink-soft); letter-spacing: 1px; margin-top: 2px; }

  .contacts { position: absolute; right: 70px; top: 165px; list-style: none; }
  .contacts li {
    display: flex; justify-content: flex-end; align-items: center; gap: 12px;
    font-size: 19px; letter-spacing: 1px; color: var(--ink); height: 38px;
  }
  .contacts svg { width: 18px; height: 18px; flex: none; }
  .icon-stroke { fill: none; stroke: var(--ink); stroke-width: 2; stroke-linecap: round; stroke-linejoin: round; }
  .icon-fill { fill: var(--ink); }

  .address {
    position: absolute; left: 55px; bottom: 42px;
    color: var(--white); font-size: 26px; letter-spacing: 1.5px; line-height: 1.35;
  }
</style>
</head>
<body>
<main class="stage">
  <section class="card" aria-label="Tovrin Advisors business card">
    <svg class="card-shapes" viewBox="0 0 1050 600" width="1050" height="600" aria-hidden="true">
      <rect class="corner-tab" x="1000" y="62" width="50" height="40"/>
      <path class="swoosh-dark" d="M540,470 C740,455 900,400 1050,325 L1050,348 C900,425 740,468 540,472 Z"/>
      <path class="swoosh-green" d="M0,345 C330,470 760,480 1050,380 L1050,600 L0,600 Z"/>
    </svg>

    <div class="brand">
      <div class="brand-row">
        <span class="brand-dot"></span>
        <span class="brand-name">Tovrin Advisors</span>
      </div>
      <p class="brand-tagline">Sustainable building energy &amp; development services</p>
    </div>

    <div class="person">
      <h1 class="person-name">MARK J. HALVIK</h1>
      <p class="person-title">Principal + Founder</p>
    </div>

    <ul class="contacts">
      <li>555.814.0627
        <svg viewBox="0 0 24 24"><path class="icon-fill" d="M6.6 10.8a15 15 0 0 0 6.6 6.6l2.2-2.2a1 1 0 0 1 1-.25 11.4 11.4 0 0 0 3.6.6 1 1 0 0 1 1 1V20a1 1 0 0 1-1 1A17 17 0 0 1 3 4a1 1 0 0 1 1-1h3.5a1 1 0 0 1 1 1c0 1.25.2 2.45.57 3.57a1 1 0 0 1-.25 1z"/></svg>
      </li>
      <li>mhalvik@tovrin-advisors.example
        <svg viewBox="0 0 24 24"><rect class="icon-fill" x="2" y="5" width="20" height="14" rx="1.5"/><path d="M3 6l9 7 9-7" fill="none" stroke="#fff" stroke-width="1.8"/></svg>
      </li>
      <li>www.tovrin-advisors.example
        <svg viewBox="0 0 24 24"><circle class="icon-stroke" cx="12" cy="12" r="9.5"/><ellipse class="icon-stroke" cx="12" cy="12" rx="4" ry="9.5"/><line class="icon-stroke" x1="2.5" y1="12" x2="21.5" y2="12"/></svg>
      </li>
    </ul>

    <p class="address">San Francisco,<br>California</p>
  </section>
</main>
</body>
</html>
```